Business Card Design for company

We want new business cards. We'd like something different-- yet still highly professional. Our tagline is Providing leadership, delivering success. Stock photos are ok, as long as they are relevant and look upscale.

Target Market(s)

Architecture/Business Management Consulting/Engineering Consulting

Contact Information for Business Card

dark gray background with pops of blue might be good, but you tell me. You're the designers. Rounded corners might be nice, but again, you tell me.

Font styles to use
Serif
Sans Serif

Colors
3276b5
5c5c5c
9d9d9d
fbfbfb

Requirements
Nice to have
• Something different, but still very professional.

```html
<!DOCTYPE html>
<html lang="en">
<head>
<meta charset="utf-8">
<title>Norland Advisory – Business Card</title>
<link rel="stylesheet" href="https://fonts.googleapis.com/css2?family=Open+Sans:wght@400;600&display=swap">
<style>
  :root {
    --brand-blue: #3276b5;
    --brand-blue-light: #4a8cc6;
    --charcoal: #5c5c5c;
    --mid-gray: #9d9d9d;
    --paper: #fbfbfb;
    --ink: #1e1e1e;
    --backdrop: #e6e6e6;
  }
  * { margin: 0; padding: 0; box-sizing: border-box; }
  html, body {
    width: 1200px; height: 1023px; overflow: hidden;
    background: var(--backdrop);
    font-family: "Open Sans", Arial, sans-serif;
  }
  .card {
    position: absolute; left: 150px; top: 254px;
    width: 900px; height: 514px;
    background: var(--paper);
    box-shadow: 0 10px 30px rgba(0,0,0,.18);
    overflow: hidden;
  }
  .card__identity {
    position: absolute; left: 0; top: 0; width: 100%; height: 300px;
  }
  .brand-name {
    position: absolute; left: 70px; top: 110px;
    font-size: 52px; font-weight: 600; color: var(--charcoal);
    letter-spacing: 1px; line-height: 1;
  }
  .brand-name__sub {
    display: block; margin-top: 14px;
    font-size: 52px;
  }
  .holder {
    position: absolute; right: 70px; top: 70px; text-align: right;
  }
  .holder__name { font-size: 34px; font-weight: 600; color: var(--ink); line-height: 1.1; }
  .holder__role { font-size: 22px; color: var(--ink); margin-top: 2px; }
  .card__rule {
    position: absolute; left: 0; top: 300px; width: 100%; height: 18px;
    background: var(--charcoal);
  }
  .card__contact {
    position: absolute; left: 0; top: 318px; width: 100%; height: 196px;
    background: linear-gradient(100deg, var(--brand-blue-light), var(--brand-blue) 60%);
    color: #fff;
  }
  .contact-list {
    position: absolute; left: 60px; top: 38px; list-style: none;
  }
  .contact-list li {
    display: flex; align-items: center; gap: 14px;
    font-size: 23px; line-height: 40px;
  }
  .icon { width: 24px; height: 24px; flex: none; }
  .divider {
    position: absolute; left: 450px; top: 48px; width: 2px; height: 100px;
    background: #fff;
  }
  .address {
    position: absolute; left: 500px; top: 38px;
    display: flex; gap: 14px; font-size: 23px; line-height: 36px;
  }
  .address .icon { margin-top: 6px; }
</style>
</head>
<body>
  <main class="card">
    <section class="card__identity">
      <div class="brand-name">NORLAND<span class="brand-name__sub">ADVISORY</span></div>
      <div class="holder">
        <div class="holder__name">Daniel Ward</div>
        <div class="holder__role">Owner</div>
      </div>
    </section>
    <div class="card__rule"></div>
    <section class="card__contact">
      <ul class="contact-list">
        <li>
          <svg class="icon" viewBox="0 0 24 24"><rect width="24" height="24" rx="4" fill="#fff"/><path d="M8 6c-1 1-1.5 2-1 3.5 1 3 4 6 7 7 1.5.5 2.5 0 3.5-1l-2-2-1.5 1c-1.5-.7-3-2.2-3.7-3.7l1-1.5z" fill="#3276b5"/></svg>
          +0000-0000-0000
        </li>
        <li>
          <svg class="icon" viewBox="0 0 24 24"><rect width="24" height="24" rx="4" fill="#fff"/><rect x="5" y="7" width="14" height="10" fill="none" stroke="#3276b5" stroke-width="1.8"/><path d="M5 7l7 6 7-6" fill="none" stroke="#3276b5" stroke-width="1.8"/></svg>
          info@yourdomain.com
        </li>
        <li>
          <svg class="icon" viewBox="0 0 24 24"><rect width="24" height="24" rx="4" fill="#fff"/><circle cx="12" cy="12" r="6.5" fill="none" stroke="#3276b5" stroke-width="1.8"/><path d="M5.5 12h13M12 5.5c-3 3.5-3 9.5 0 13M12 5.5c3 3.5 3 9.5 0 13" fill="none" stroke="#3276b5" stroke-width="1.4"/></svg>
          www.yourdomain.com
        </li>
      </ul>
      <div class="divider"></div>
      <div class="address">
        <svg class="icon" viewBox="0 0 24 24"><rect width="24" height="24" rx="4" fill="#fff"/><path d="M12 5a5 5 0 0 0-5 5c0 4 5 9 5 9s5-5 5-9a5 5 0 0 0-5-5z" fill="#3276b5"/><circle cx="12" cy="10" r="2" fill="#fff"/></svg>
        <div>Suite 210,<br>48 Harbour Lane,<br>Bristol</div>
      </div>
    </section>
  </main>
</body>
</html>
```